Solar Company Bussiness Card

I need a 2 sided business card and would like a .psd and any font files for each side of the card. I would like my logo used, it should be attached with the fonts. I'm not opposed to the font colors with the logo being changed.

On the sample design, I'd like the following:

Marcus Dellow
President
Phone: 555-382-9174
www.brightvanepower.example

As I've recently opened in a 2nd market, I'm not sure about an address as I currently have 2 of them. I may actually get separate cards printed, one batch for each address, that's why I need the PSD file.
Updates

I'm very pleased with the response and designs I've received here for my business card. First and foremost, I'd like to thank everyone who took the time to submit a design. There truly are a lot of great designs in the bunch here and I'm having a little difficulty deciding. I will be reaching out to someone in the next day or two here to go to a final design. At this time, I'm not looking for any new concepts. If any of you do logos, I'm looking for a new logo for our sister entity, Dellow Partners, Inc. Thanks, Marcus Dellow

Reason: I'm not looking for any new designs at this point, but extending this deadline in order to give people I've asked a chance to re-submit items.

Industry/Entity Type

Business

```html
<!DOCTYPE html>
<html lang="en">
<head>
<meta charset="utf-8">
<title>Brightvane Power – Business Card</title>
<link rel="stylesheet" href="https://fonts.googleapis.com/css2?family=Ubuntu:wght@400;500&display=swap">
<style>
  :root {
    --page-bg: #e6e7e9;
    --card-bg: #ffffff;
    --brand-blue: #1f5fb3;
    --brand-blue-light: #5aa8e6;
    --brand-blue-deep: #0f4a9e;
    --ink: #2a2a2a;
    --ink-soft: #4a4a4a;
    --shadow: rgba(0, 0, 0, 0.18);
  }
  * { box-sizing: border-box; margin: 0; padding: 0; }
  html, body {
    width: 1200px;
    height: 871px;
    overflow: hidden;
    background: var(--page-bg);
    font-family: "Ubuntu", "Verdana", sans-serif;
  }
  .canvas {
    position: relative;
    width: 1200px;
    height: 871px;
  }
  .card {
    position: absolute;
    width: 560px;
    height: 320px;
    background: var(--card-bg);
    box-shadow: 0 10px 30px var(--shadow);
    overflow: hidden;
  }
  .card--front { left: 90px; top: 90px; }
  .card--back { left: 550px; top: 461px; }

  .brand {
    position: absolute;
    display: flex;
    align-items: center;
    gap: 10px;
    color: var(--brand-blue);
    font-weight: 500;
    white-space: nowrap;
  }
  .brand__mark {
    width: 18px;
    height: 18px;
    background: var(--brand-blue);
  }
  .card--front .brand { left: 48px; top: 118px; font-size: 34px; }
  .card--back .brand { left: 34px; top: 138px; font-size: 22px; gap: 8px; }
  .card--back .brand__mark { width: 13px; height: 13px; }

  .front__decor {
    position: absolute;
    right: 0;
    top: 0;
    width: 240px;
    height: 320px;
  }

  .contact {
    position: absolute;
    left: 272px;
    top: 106px;
    width: 256px;
    color: var(--ink);
  }
  .contact__name {
    font-size: 20px;
    font-weight: 400;
    letter-spacing: 0.5px;
  }
  .contact__title {
    font-size: 13px;
    color: var(--brand-blue);
    margin-top: 3px;
    margin-bottom: 18px;
  }
  .contact__line {
    display: flex;
    align-items: center;
    gap: 12px;
    font-size: 14px;
    color: var(--ink-soft);
    letter-spacing: 0.3px;
    margin-bottom: 10px;
    white-space: nowrap;
  }
  .contact__icon { width: 15px; height: 15px; flex: none; }
</style>
</head>
<body>
<main class="canvas">

  <section class="card card--front" aria-label="Card front">
    <div class="brand">
      <span class="brand__mark"></span>
      <span class="brand__name">Brightvane Power</span>
    </div>
    <svg class="front__decor" viewBox="0 0 240 320" role="img" aria-label="Large blue brand graphic in the corner">
      <defs>
        <linearGradient id="decorFill" x1="0" y1="0" x2="1" y2="1">
          <stop offset="0" stop-color="#5aa8e6"/>
          <stop offset="1" stop-color="#1f5fb3"/>
        </linearGradient>
      </defs>
      <polygon points="150,0 240,0 240,320 40,320" fill="url(#decorFill)"/>
    </svg>
  </section>

  <section class="card card--back" aria-label="Card back">
    <div class="brand">
      <span class="brand__mark"></span>
      <span class="brand__name">Brightvane Power</span>
    </div>
    <div class="contact">
      <p class="contact__name">Marcus Dellow</p>
      <p class="contact__title">President</p>
      <p class="contact__line">
        <svg class="contact__icon" viewBox="0 0 16 16" aria-hidden="true">
          <path d="M2 5 Q8 1 14 5 L12 7 L10 6 L10 5 Q8 4 6 5 L6 6 L4 7 Z" fill="var(--brand-blue)"/>
          <rect x="4" y="8" width="8" height="6" rx="1.5" fill="var(--brand-blue)"/>
          <circle cx="8" cy="11" r="1.5" fill="#fff"/>
        </svg>
        <span>555-382-9174</span>
      </p>
      <p class="contact__line">
        <svg class="contact__icon" viewBox="0 0 16 16" aria-hidden="true">
          <circle cx="8" cy="8" r="6.5" fill="none" stroke="var(--brand-blue)" stroke-width="1.6"/>
          <ellipse cx="8" cy="8" rx="2.8" ry="6.5" fill="none" stroke="var(--brand-blue)" stroke-width="1.2"/>
          <line x1="1.5" y1="8" x2="14.5" y2="8" stroke="var(--brand-blue)" stroke-width="1.2"/>
        </svg>
        <span>www.brightvanepower.example</span>
      </p>
    </div>
  </section>

</main>
</body>
</html>
```